Flyer Design Project for psychologist

I need an A4 flyer designed for a new psychology practice I am setting up called Harbour Bloom. The focus is to cater for the mental health and well-being of mums throughout their life stages, to help them live their best life whilst providing support and guidance in their journey through Motherhood.
The flyer will be used to promote the main services we provide and will echo the look and feel of website (www.harbourbloom.com.au) and logo design. Images/photos can be downloaded off the Harbour Bloom website homepage slider or on "Our Services" page.
Corporate colours
Colours:
Bright green: Pantone 376
Bright green as CMYK: c: 45.2% m: 0% y: 100% k: 0%
Logo text large grey: 70% black
Logo text strapline: 75% black
Tree: 80% black
Fonts:
Logo 'Harbour Bloom': Verdana
Logo 'Counselling & coaching services for mums': Gill Sans Light
Updates
OMG you are all awesome!!!! Will be very very hard decision :-(
Target Market(s)
Mothers - all life stages wanting support counselling
Industry/Entity Type
Mental Health
Look and feel
Each slider illustrates characteristics of the customer's brand and the style your logo design should communicate.

```html
<!DOCTYPE html>
<html lang="en">
<head>
<meta charset="utf-8">
<title>Harbour Bloom – Counselling and Coaching for Mums</title>
<link rel="stylesheet" href="https://fonts.googleapis.com/css2?family=Noto+Sans:wght@400;700&family=Lato:wght@300;400&display=swap">
<style>
  :root {
    --green: #7be300;
    --grey-dark: #4a4a4a;
    --grey-text: #555555;
    --hero-light: #f7f7f5;
    --hero-sea: #dfe3e4;
    --white: #ffffff;
  }
  * { margin: 0; padding: 0; box-sizing: border-box; }
  html, body { width: 849px; height: 1200px; overflow: hidden; background: var(--white); }
  .flyer { position: relative; width: 849px; height: 1200px; overflow: hidden; background: var(--white); }

  .hero {
    position: absolute; left: 0; top: 0; width: 849px; height: 452px;
    background:
      radial-gradient(ellipse 170px 230px at 665px 250px, #efe9dc 0%, rgba(239,233,220,0) 100%),
      linear-gradient(180deg, var(--white) 0%, var(--hero-light) 55%, var(--hero-sea) 82%, #eeeeec 100%);
  }
  .hero-photo {
    position: absolute; left: 500px; top: 40px; width: 349px; height: 412px;
    background: linear-gradient(180deg, rgba(240,236,226,0.6) 0%, rgba(225,220,205,0.55) 55%, rgba(150,170,195,0.45) 100%);
  }

  .brand {
    position: absolute; left: 53px; top: 112px;
    display: flex; align-items: center; gap: 14px;
  }
  .brand-name {
    font-family: "Noto Sans", Verdana, sans-serif; font-weight: 700;
    font-size: 42px; color: var(--grey-dark); letter-spacing: -0.5px; line-height: 1;
  }
  .brand-dot { width: 22px; height: 22px; border-radius: 50%; background: var(--green); }

  .headline {
    position: absolute; left: 53px; top: 250px; width: 560px;
    font-family: "Noto Sans", Verdana, sans-serif; font-weight: 700;
    font-size: 32px; line-height: 41px; color: var(--grey-dark);
  }

  .band { position: absolute; left: 0; width: 849px; background: var(--green); }
  .band-top { top: 452px; height: 26px; }
  .band-mid { top: 1011px; height: 26px; }
  .band-bottom { top: 1173px; height: 27px; }

  .intro {
    position: absolute; left: 50px; top: 512px; width: 750px;
    font-family: Lato, "Gill Sans", sans-serif; font-weight: 300;
    font-size: 17.5px; line-height: 25.6px; color: var(--grey-text);
  }
  .intro p { margin-bottom: 25.6px; }

  .services {
    position: absolute; top: 790px; list-style: none;
    font-family: Lato, "Gill Sans", sans-serif; font-weight: 300;
    font-size: 17.5px; line-height: 25.6px; color: var(--grey-text);
  }
  .services li { position: relative; padding-left: 27px; }
  .services li::before { content: "•"; position: absolute; left: 3px; }
  .services-left { left: 50px; }
  .services-right { left: 427px; }

  .contact {
    position: absolute; left: 53px; top: 958px;
    font-family: "Noto Sans", Verdana, sans-serif; font-weight: 700;
    font-size: 18.5px; color: var(--grey-dark);
  }

  .gallery { position: absolute; top: 1037px; height: 136px; }
  .gallery-mother { left: 0; width: 262px;
    background: linear-gradient(135deg, #f6e2d4 0%, #e9c2a6 50%, #f2ddd0 100%); }
  .gallery-hands { left: 265px; width: 319px;
    background: radial-gradient(ellipse 90px 50px at 150px 75px, #e86a9a 0%, #f1c7a8 55%, #e6e4e1 100%); }
  .gallery-family { left: 587px; width: 262px;
    background: linear-gradient(180deg, #5e7d3c 0%, #8a6a55 50%, #c99b84 100%); }
</style>
</head>
<body>
<main class="flyer">
  <section class="hero">
    <div class="hero-photo" role="img" aria-label="Smiling mature woman with arms raised on a bright beach"></div>
    <div class="brand">
      <span class="brand-name">Harbour Bloom</span>
      <span class="brand-dot"></span>
    </div>
    <h1 class="headline">Live your best with Harbour Bloom Counselling and Coaching for Mums</h1>
  </section>

  <div class="band band-top"></div>

  <section class="intro">
    <p>Harbour Bloom provides counselling and coaching services especially for mums. Our main focus is to help you effectively deal with the daily issues that you may face that impacts on your mental health and wellbeing whilst providing support and guidance in your journey throughout Motherhood.</p>
    <p>We help mums to uncover their strengths, set purposeful goals, develop the skills, ability and confidence that they need to be happier and lead meaningful and flourishing lives.</p>
    <p>We can provide counselling and coaching for:</p>
  </section>

  <ul class="services services-left">
    <li>Non-Directive Pregnancy Support</li>
    <li>Antenatal Depression</li>
    <li>Preparing for Baby</li>
    <li>Postnatal Depression</li>
    <li>Anxiety</li>
  </ul>
  <ul class="services services-right">
    <li>Motherhood Stress and Anger</li>
    <li>Surviving and Thriving Through a Breakup</li>
    <li>Work/Family Balance</li>
    <li>Increasing Happiness</li>
    <li>Finding Yourself in Motherhood</li>
  </ul>

  <p class="contact">Call (02) 9000 4821 or visit our website: www.harbourbloom.com.au</p>

  <div class="band band-mid"></div>
  <div class="gallery gallery-mother" role="img" aria-label="Mother and baby touching noses"></div>
  <div class="gallery gallery-hands" role="img" aria-label="Cupped hands holding colourful puzzle pieces"></div>
  <div class="gallery gallery-family" role="img" aria-label="Group of mothers with their toddlers outdoors"></div>
  <div class="band band-bottom"></div>
</main>
</body>
</html>
```